Larkfield Ridge Management

I need a professional website. My current website is larkfieldridgemanagement.com and I hate it. It was created with some AI tool very quickly because I needed a site up and running with no advanced notice. I’m open to all designs .. I trust you, the professionals will deliver the results I’m anxiously awaiting! :)

```html
<!DOCTYPE html>
<html lang="en">
<head>
<meta charset="utf-8">
<title>Larkfield Ridge Management</title>
<link rel="stylesheet" href="https://fonts.googleapis.com/css2?family=Poppins:wght@400;500;600;700&display=swap">
<style>
:root{
  --navy:#27375f;
  --navy-dark:#1d2a4b;
  --red:#8b1a2b;
  --ink:#1f1f1f;
  --muted:#555;
  --black:#0c0c0c;
  --white:#fff;
}
*{margin:0;padding:0;box-sizing:border-box}
html,body{width:1200px;height:4378px;overflow:hidden}
body{font-family:"Poppins",sans-serif;color:var(--ink);background:var(--white);position:relative}
.abs{position:absolute}
.btn{position:absolute;display:flex;align-items:center;justify-content:center;font-size:11px;font-weight:600;color:var(--white);background:var(--red);clip-path:polygon(8% 0,100% 0,92% 100%,0 100%);letter-spacing:.2px}
.btn.light{background:var(--white);color:var(--navy)}
.eyebrow{font-size:13px;color:var(--red);font-weight:500;text-transform:uppercase}
.h2{font-size:33px;font-weight:600;color:var(--ink);text-transform:uppercase}
.p{font-size:12.5px;line-height:19.5px;color:var(--muted)}
.brand{font-weight:700;color:var(--white);text-align:center;line-height:1.15}

.header-left{left:0;top:0;width:425px;height:125px;background:var(--navy);clip-path:polygon(0 0,395px 0,425px 125px,0 125px)}
.contact-item{display:flex;align-items:center;gap:12px;top:18px}
.contact-icon{width:40px;height:40px;background:var(--red);transform:rotate(45deg);display:flex;align-items:center;justify-content:center;border-radius:4px}
.contact-icon svg{transform:rotate(-45deg)}
.contact-label{font-size:11px;color:#555}
.contact-value{font-size:15px;font-weight:500;color:var(--ink)}
.navbar{left:425px;top:82px;width:775px;height:43px;background:var(--black);font-size:13px;color:var(--white);font-weight:500}
.navbar span{position:absolute;top:13px}

.hero{left:0;top:125px;width:1200px;height:615px;
  background:
    linear-gradient(90deg,rgba(20,35,25,.55) 0%,rgba(20,35,25,.25) 45%,rgba(0,0,0,0) 70%),
    radial-gradient(ellipse 420px 260px at 78% 45%,#b9a58f 0%,rgba(160,140,120,.6) 45%,rgba(0,0,0,0) 75%),
    radial-gradient(ellipse 500px 300px at 25% 70%,#3e5a33 0%,rgba(62,90,51,0) 80%),
    linear-gradient(165deg,#4e6a40 0%,#617653 40%,#8a8576 65%,#5d6a57 100%);
  clip-path:polygon(0 0,100% 0,100% 86%,0 100%)}
.hero-title{left:158px;top:265px;font-size:42px;line-height:53px;font-weight:600;color:var(--white);text-transform:uppercase}
.hero-sub{left:162px;top:428px;font-size:13px;color:var(--white)}

.services{left:0;top:1965px;width:1200px;height:655px;background:var(--navy);clip-path:polygon(0 0,100% 0,100% 88%,0 100%)}
.card{position:absolute;top:2166px;width:208px;height:270px;background:var(--white)}
.card .ph{height:228px}
.card .label{height:42px;display:flex;align-items:center;justify-content:center;font-size:14px;font-weight:600;color:var(--ink)}

.check-list{left:160px;top:2816px;list-style:none}
.check-list li{display:flex;align-items:center;gap:14px;height:36px;font-size:14.5px;color:#444}

.foot-h{font-size:15px;font-weight:600;color:var(--white);text-transform:uppercase}
.foot-l{font-size:13px;color:#dfe4ee}
</style>
</head>
<body>

<div class="abs header-left"></div>
<div class="abs brand" style="left:150px;top:40px;width:125px;font-size:16px">LARKFIELD RIDGE<br><span style="font-size:10px;font-weight:500">MANAGEMENT</span></div>

<div class="abs contact-item" style="left:510px">
  <div class="contact-icon"><svg width="18" height="18" viewBox="0 0 24 24"><path fill="#fff" d="M6.6 10.8a15 15 0 0 0 6.6 6.6l2.2-2.2a1 1 0 0 1 1-.25 11.4 11.4 0 0 0 3.6.57 1 1 0 0 1 1 1V20a1 1 0 0 1-1 1A17 17 0 0 1 3 4a1 1 0 0 1 1-1h3.5a1 1 0 0 1 1 1c0 1.25.2 2.45.57 3.57a1 1 0 0 1-.25 1z"/></svg></div>
  <div><div class="contact-label">Call Us</div><div class="contact-value">555-014-2837</div></div>
</div>
<div class="abs contact-item" style="left:694px">
  <div class="contact-icon"><svg width="18" height="18" viewBox="0 0 24 24"><rect x="3" y="6" width="18" height="12" rx="1" fill="#fff"/><path d="M3 7l9 6 9-6" stroke="#8b1a2b" stroke-width="1.6" fill="none"/></svg></div>
  <div><div class="contact-label">E-Mail</div><div class="contact-value">info@larkfieldridgemanagement.com</div></div>
</div>

<nav class="abs navbar">
  <span style="left:62px">Home</span>
  <span style="left:171px">About Us</span>
  <span style="left:303px">Services</span>
  <span style="left:430px">News</span>
  <span style="left:540px">Contact Us</span>
</nav>

<div class="abs hero" role="img" aria-label="Aerial photo of a large campus of buildings surrounded by trees"></div>
<svg class="abs" style="left:0;top:640px" width="1200" height="110"><polygon points="0,98 1200,8 1200,18 0,106" fill="#27375f"/></svg>
<svg class="abs" style="left:25px;top:400px" width="20" height="24"><path d="M14 3L5 12l9 9" stroke="#fff" stroke-width="2" fill="none"/></svg>
<svg class="abs" style="left:1155px;top:400px" width="20" height="24"><path d="M6 3l9 9-9 9" stroke="#fff" stroke-width="2" fill="none"/></svg>
<h1 class="abs hero-title">Professional Property<br>Management You<br>Can Trust</h1>
<div class="abs hero-sub">A true partner, not just a vendor.</div>
<div class="btn" style="left:162px;top:470px;width:228px;height:37px">GET A FREE CONSULTATION</div>

<div class="abs" style="left:161px;top:805px;width:439px;height:410px;background:
  radial-gradient(ellipse 160px 200px at 28% 35%,#8d8f93 0%,rgba(141,143,147,0) 80%),
  radial-gradient(ellipse 140px 220px at 88% 30%,#2e3446 0%,rgba(46,52,70,0) 85%),
  radial-gradient(ellipse 260px 110px at 50% 88%,#eef0ee 0%,rgba(238,240,238,0) 80%),
  radial-gradient(ellipse 200px 80px at 55% 78%,#5d7f3a 0%,rgba(93,127,58,0) 80%),
  linear-gradient(180deg,#c8ccd1,#dfe2e5 60%,#e9ebec);box-shadow:0 6px 18px rgba(0,0,0,.12)" role="img" aria-label="Photo of two business people shaking hands over a model of buildings and trees"></div>
<div class="abs eyebrow" style="left:681px;top:862px">Why Choose Us</div>
<h2 class="abs h2" style="left:681px;top:882px">About Us</h2>
<p class="abs p" style="left:681px;top:938px;width:365px">Lorem Ipsum is simply dummy text of the printing and typesetting industry. Lorem Ipsum has been the industry's standard dummy text ever since the 1500s, when an unknown printer took a galley of type and scrambled it to make a type specimen book. It has survived not only five centuries, but also the leap into electronic typesetting, remaining essentially unchanged. It was popularised in the 1960.</p>
<div class="btn" style="left:681px;top:1120px;width:153px;height:36px">LEARN MORE</div>

<div class="abs" style="left:0;top:1500px;width:1200px;height:465px;background:linear-gradient(180deg,rgba(255,255,255,1) 0%,rgba(226,230,236,.9) 40%,rgba(205,211,220,.9) 100%)" role="img" aria-label="Faint city skyline backdrop"></div>
<div class="abs eyebrow" style="left:0;width:1200px;text-align:center;top:1287px">Your Partners in Growth</div>
<h2 class="abs h2" style="left:0;width:1200px;text-align:center;top:1305px">How It Works</h2>
<p class="abs p" style="left:410px;width:380px;text-align:center;top:1355px">Lorem Ipsum is simply dummy text of the printing and typesetting industry.</p>

<svg class="abs" style="left:570px;top:1430px" width="60" height="64" viewBox="0 0 60 64"><rect x="16" y="2" width="28" height="38" fill="#8b1a2b"/><g fill="#fff"><rect x="21" y="8" width="5" height="5"/><rect x="34" y="8" width="5" height="5"/><rect x="21" y="18" width="5" height="5"/><rect x="34" y="18" width="5" height="5"/><rect x="27" y="30" width="6" height="10"/></g><path d="M4 46c10-4 18 2 26 2h10c4 0 4 5 0 5H28M4 58l16 4 34-12" stroke="#8b1a2b" stroke-width="4" fill="none"/></svg>
<div class="abs" style="left:400px;width:400px;text-align:center;top:1508px;font-size:16px;font-weight:600">Property Assessment</div>
<p class="abs p" style="left:450px;width:300px;text-align:center;top:1535px">Lorem Ipsum is simply dummy text of the printing and typesetting industry.</p>

<svg class="abs" style="left:160px;top:1550px" width="56" height="56" viewBox="0 0 24 24"><path fill="#27375f" d="M6.6 10.8a15 15 0 0 0 6.6 6.6l2.2-2.2a1 1 0 0 1 1-.25 11.4 11.4 0 0 0 3.6.57 1 1 0 0 1 1 1V20a1 1 0 0 1-1 1A17 17 0 0 1 3 4a1 1 0 0 1 1-1h3.5a1 1 0 0 1 1 1c0 1.25.2 2.45.57 3.57a1 1 0 0 1-.25 1z"/></svg>
<div class="abs" style="left:163px;top:1620px;font-size:16px;font-weight:600">Schedule a Consultation</div>
<p class="abs p" style="left:163px;top:1647px;width:290px">Lorem Ipsum is simply dummy text of the printing and typesetting industry.</p>

<svg class="abs" style="left:980px;top:1550px" width="58" height="56" viewBox="0 0 58 56"><g fill="#27375f"><rect x="4" y="38" width="7" height="14"/><rect x="15" y="30" width="7" height="22"/><rect x="26" y="22" width="7" height="30"/><rect x="37" y="14" width="7" height="38"/></g><path d="M2 36L44 6" stroke="#27375f" stroke-width="3"/><path d="M40 3l9-1-2 9z" fill="#27375f"/></svg>
<div class="abs" style="left:740px;width:298px;text-align:right;top:1620px;font-size:16px;font-weight:600">Reports &amp; Support</div>
<p class="abs p" style="left:748px;top:1647px;width:290px;text-align:right">Lorem Ipsum is simply dummy text of the printing and typesetting industry.</p>

<svg class="abs" style="left:360px;top:1535px" width="60" height="40"><path d="M4 36C15 18 30 10 54 8" stroke="#4d6fa5" stroke-width="2" fill="none"/><path d="M46 3l10 5-10 5" stroke="#4d6fa5" stroke-width="2" fill="none"/></svg>
<svg class="abs" style="left:770px;top:1540px" width="60" height="40"><path d="M4 6c18 0 32 8 46 24" stroke="#4d6fa5" stroke-width="2" fill="none"/><path d="M52 20l0 12-11-2" stroke="#4d6fa5" stroke-width="2" fill="none"/></svg>

<div class="abs" style="left:420px;top:1585px;width:360px;height:380px;background:
  radial-gradient(ellipse 150px 230px at 50% 75%,rgba(39,55,95,.95) 0%,rgba(39,55,95,.6) 45%,rgba(39,55,95,0) 80%),
  radial-gradient(ellipse 110px 90px at 60% 18%,rgba(196,170,150,.55) 0%,rgba(196,170,150,0) 80%)" role="img" aria-label="Photo of a smiling businesswoman and businessman standing back to back"></div>
<div class="abs brand" style="left:450px;top:1860px;width:300px;font-size:24px">LARKFIELD RIDGE<br><span style="font-size:13px;font-weight:500">MANAGEMENT</span></div>

<div class="abs services"></div>
<div class="abs" style="left:0;width:1200px;text-align:center;top:2016px;font-size:13px;color:#fff">OUR SERVICES</div>
<h2 class="abs h2" style="left:0;width:1200px;text-align:center;top:2034px;color:#fff">Services We Offer</h2>
<p class="abs p" style="left:250px;width:700px;text-align:center;top:2085px;color:#e6e9f0">Lorem Ipsum is simply dummy text of the printing and typesetting industry. Lorem Ipsum has been the industry's standard dummy text ever since the 1500.</p>

<div class="card" style="left:163px"><div class="ph" style="background:radial-gradient(ellipse 90px 60px at 40% 75%,#e0b780 0%,rgba(224,183,128,0) 80%),linear-gradient(180deg,#3f4a5c 0%,#8f8c87 45%,#d9d6d0 60%,#5b5650 100%)" role="img" aria-label="Photo of a modern residential house at dusk"></div><div class="label">Residential Property</div></div>
<div class="card" style="left:385px"><div class="ph" style="background:radial-gradient(ellipse 70px 130px at 65% 60%,#2f6f9a 0%,rgba(47,111,154,0) 85%),linear-gradient(180deg,#b9d8ef 0%,#8dbad9 40%,#4b7d9c 75%,#3a5c6e 100%)" role="img" aria-label="Photo of glass commercial office towers"></div><div class="label">Commercial Property</div></div>
<div class="card" style="left:607px"><div class="ph" style="background:radial-gradient(ellipse 60px 90px at 25% 55%,#b7c2cc 0%,rgba(183,194,204,0) 85%),radial-gradient(ellipse 60px 110px at 85% 60%,#3a3f48 0%,rgba(58,63,72,0) 85%),linear-gradient(180deg,#f1f3f5,#dfe4e8 60%,#c4ccd3)" role="img" aria-label="Photo of a couple receiving house keys from an agent"></div><div class="label">Tenant Placement</div></div>
<div class="card" style="left:829px"><div class="ph" style="background:radial-gradient(ellipse 60px 120px at 45% 55%,#a98a55 0%,rgba(169,138,85,0) 85%),linear-gradient(180deg,#5a6578 0%,#3a4252 50%,#262c38 100%)" role="img" aria-label="Photo of a lit high-rise apartment tower at night"></div><div class="label">Maintenance Coordination</div></div>

<div class="btn" style="left:515px;top:2482px;width:170px;height:36px">VIEW ALL SERVICES</div>

<div class="abs eyebrow" style="left:160px;top:2678px">Property Management Solutions</div>
<h2 class="abs h2" style="left:160px;top:2695px">Industries We Serve</h2>
<p class="abs p" style="left:161px;top:2748px;width:370px">Lorem Ipsum is simply dummy text of the printing and typesetting industry.</p>
<ul class="abs check-list">
  <li><svg width="20" height="18"><path d="M2 9l6 6L18 2" stroke="#27375f" stroke-width="3" fill="none"/></svg>Residential Property</li>
  <li><svg width="20" height="18"><path d="M2 9l6 6L18 2" stroke="#27375f" stroke-width="3" fill="none"/></svg>Commercial Property</li>
  <li><svg width="20" height="18"><path d="M2 9l6 6L18 2" stroke="#27375f" stroke-width="3" fill="none"/></svg>Tenant Placement</li>
  <li><svg width="20" height="18"><path d="M2 9l6 6L18 2" stroke="#27375f" stroke-width="3" fill="none"/></svg>Maintenance Coordination</li>
  <li><svg width="20" height="18"><path d="M2 9l6 6L18 2" stroke="#27375f" stroke-width="3" fill="none"/></svg>Financial Reporting</li>
  <li><svg width="20" height="18"><path d="M2 9l6 6L18 2" stroke="#27375f" stroke-width="3" fill="none"/></svg>Manufacturing</li>
</ul>
<div class="btn" style="left:161px;top:3053px;width:153px;height:37px">SEE MORE</div>
<div class="abs" style="left:600px;top:2680px;width:438px;height:410px;background:radial-gradient(ellipse 60px 160px at 52% 55%,#6f8197 0%,rgba(111,129,151,0) 85%),linear-gradient(180deg,#4f86c8 0%,#9fc0e2 30%,#cfdbe6 45%,#8d96a2 65%,#4c5562 100%);box-shadow:0 6px 18px rgba(0,0,0,.12)" role="img" aria-label="Aerial photo of a dense city skyline with skyscrapers"></div>

<div class="abs" style="left:0;top:3110px;width:1200px;height:300px;background:linear-gradient(180deg,#fff,#d5dae2)" role="img" aria-label="Faint city skyline backdrop"></div>
<div class="abs" style="left:0;top:3240px;width:1200px;height:700px;background:
  radial-gradient(ellipse 300px 380px at 73% 48%,rgba(140,110,90,.75) 0%,rgba(90,80,80,.45) 50%,rgba(0,0,0,0) 85%),
  linear-gradient(100deg,#243050 0%,#2f3a58 40%,#3d4560 65%,#2a3147 100%);
  clip-path:polygon(0 130px,1200px 0,1200px 100%,0 100%)" role="img" aria-label="Photo of a smiling man in a sweater looking at his smartphone"></div>
<div class="abs" style="left:160px;top:3444px;font-size:13px;color:#fff;font-weight:500">PROPERTY MANAGEMENT SOLUTIONS</div>
<h2 class="abs" style="left:158px;top:3462px;font-size:56px;line-height:62px;font-weight:600;color:#fff">BUILD CREDIBILITY<br>&amp; TRUST</h2>
<p class="abs p" style="left:161px;top:3598px;width:380px;color:#eef">Lorem Ipsum is simply dummy text of the printing and typesetting industry.</p>
<div class="btn light" style="left:163px;top:3665px;width:153px;height:38px">GET IN TOUCH</div>

<div class="abs" style="left:0;top:3720px;width:1200px;height:658px;background:var(--navy);clip-path:polygon(0 0,100% 180px,100% 100%,0 100%)"></div>
<h2 class="abs" style="left:0;width:1200px;text-align:center;top:3898px;font-size:31px;font-weight:600;color:#fff">NEWSLETTER SIGN UP</h2>
<p class="abs" style="left:320px;width:560px;text-align:center;top:3950px;font-size:11.5px;line-height:16px;color:#e6e9f0">It is a long established fact that a reader will be distracted by the readable content of a page when looking at its layout.</p>
<div class="abs" style="left:305px;top:4018px;width:427px;height:35px;background:#eef0f3;font-size:11.5px;color:#555;padding:10px 16px">Email Address</div>
<div class="abs" style="left:742px;top:4018px;width:154px;height:35px;background:var(--red);color:#fff;font-size:11px;font-weight:600;display:flex;align-items:center;justify-content:center">SUBSCRIBE NOW</div>
<div class="abs" style="left:190px;top:4125px;width:850px;height:1px;background:rgba(255,255,255,.2)"></div>

<div class="abs brand" style="left:180px;top:4205px;width:140px;font-size:16px">LARKFIELD RIDGE<br><span style="font-size:10px;font-weight:500">MANAGEMENT</span></div>
<div class="abs" style="left:198px;top:4294px;width:14px;height:14px;border-radius:50%;border:1.5px solid #fff"></div>
<div class="abs" style="left:242px;top:4294px;width:14px;height:14px;border-radius:50%;border:1.5px solid #fff"></div>
<div class="abs" style="left:284px;top:4294px;width:14px;height:14px;border-radius:50%;border:1.5px solid #fff"></div>

<div class="abs foot-h" style="left:421px;top:4156px">Quick Links</div>
<div class="abs foot-l" style="left:421px;top:4196px">Home</div>
<div class="abs foot-l" style="left:421px;top:4234px">About Us</div>
<div class="abs foot-l" style="left:421px;top:4272px">Services</div>
<div class="abs foot-l" style="left:421px;top:4310px">Contact Us</div>

<div class="abs foot-h" style="left:590px;top:4156px">Services</div>
<div class="abs foot-l" style="left:590px;top:4196px">Residential Property</div>
<div class="abs foot-l" style="left:590px;top:4234px">Commercial Property</div>
<div class="abs foot-l" style="left:590px;top:4272px">Tenant Placement</div>
<div class="abs foot-l" style="left:590px;top:4310px">Maintenance Coordination</div>

<div class="abs foot-h" style="left:818px;top:4156px">Contact Us</div>
<div class="abs" style="left:818px;top:4198px;width:26px;height:26px;border-radius:50%;background:#fff;display:flex;align-items:center;justify-content:center"><svg width="14" height="14" viewBox="0 0 24 24"><path fill="#27375f" d="M6.6 10.8a15 15 0 0 0 6.6 6.6l2.2-2.2a1 1 0 0 1 1-.25 11.4 11.4 0 0 0 3.6.57 1 1 0 0 1 1 1V20a1 1 0 0 1-1 1A17 17 0 0 1 3 4a1 1 0 0 1 1-1h3.5a1 1 0 0 1 1 1c0 1.25.2 2.45.57 3.57a1 1 0 0 1-.25 1z"/></svg></div>
<div class="abs foot-l" style="left:855px;top:4203px">555-014-2837</div>
<div class="abs" style="left:818px;top:4235px;width:26px;height:26px;border-radius:50%;background:#fff;display:flex;align-items:center;justify-content:center"><svg width="14" height="14" viewBox="0 0 24 24"><rect x="2" y="5" width="20" height="14" rx="1" fill="#27375f"/><path d="M2 6l10 7 10-7" stroke="#fff" stroke-width="1.6" fill="none"/></svg></div>
<div class="abs foot-l" style="left:855px;top:4240px">info@larkfieldridgemanagement.com</div>
<div class="abs" style="left:818px;top:4272px;width:26px;height:26px;border-radius:50%;background:#fff;display:flex;align-items:center;justify-content:center"><svg width="12" height="15" viewBox="0 0 24 30"><path fill="#27375f" d="M12 0a10 10 0 0 0-10 10c0 8 10 20 10 20s10-12 10-20A10 10 0 0 0 12 0zm0 14a4 4 0 1 1 0-8 4 4 0 0 1 0 8z"/></svg></div>
<div class="abs foot-l" style="left:855px;top:4277px">122, Lorem ipsum dolird</div>

</body>
</html>
```